Lanternfield Drinks business cards

We need a business card design for our new logo. The company is modern, progressive, professional, yet approachable. The key products are ready to drink bottles and cans of coffee based beverages.
These cards will be a critical part of the first impression made by our sales organization, business development team, and all external facing personnel.
Card can be a vertical or horizontal orientation.

Target Market(s)

Customers, suppliers, business partners

Industry/Entity Type

Business

Contact Information for Business Card

Business cards should feature Company Name and Logo.

Font styles to use
Serif

Colors

Designer to choose colors to be used in the design.

Requirements
Must have
• Strong readability of Name, phone #, mobile number and email address.
• Job title, website url, Street Address, and other details can be secondary level readability.
Nice to have
• High impact, simplistic quality design.
• Ok to utilize the 'H in the box' separate from the company name

```html
<!DOCTYPE html>
<html lang="en">
<head>
<meta charset="utf-8">
<title>Lanternfield Drinks – Business Card</title>
<link href="https://fonts.googleapis.com/css2?family=Cinzel:wght@700&family=Crimson+Text:ital,wght@0,400;0,700;1,400&display=swap" rel="stylesheet">
<style>
  :root {
    --backdrop: #3b3b3c;
    --card: #1d1d1f;
    --orange: #e2552b;
    --amber: #f0a021;
    --white: #f2f2f2;
    --silver: #8d8d90;
  }
  * { box-sizing: border-box; margin: 0; padding: 0; }
  html, body { width: 799px; height: 1200px; overflow: hidden; }
  body {
    background: var(--backdrop);
    font-family: "Crimson Text", Georgia, serif;
    position: relative;
  }
  .card {
    position: absolute;
    left: 90px;
    width: 620px;
    height: 354px;
    background: var(--card);
    box-shadow: 0 10px 28px rgba(0,0,0,.45);
    overflow: hidden;
  }
  .card--front { top: 123px; }
  .card--back { top: 723px; }

  /* front */
  .front-mark {
    position: absolute; inset: 0;
    display: flex; align-items: center; justify-content: center; gap: 22px;
  }
  .front-mark__square {
    width: 120px; height: 120px;
    border: 8px solid var(--silver);
  }
  .front-mark__name {
    font-family: "Cinzel", Georgia, serif;
    font-weight: 700; font-size: 30px; line-height: 1.15;
    color: var(--silver);
    letter-spacing: 1px;
  }

  /* back */
  .brand { position: absolute; left: 30px; top: 26px; display: flex; align-items: center; gap: 14px; }
  .brand__square { width: 62px; height: 62px; border: 4px solid var(--orange); }
  .brand__name {
    font-family: "Cinzel", Georgia, serif;
    font-weight: 700; font-size: 30px; color: var(--orange); letter-spacing: 1px;
  }
  .brand__rule {
    position: absolute; left: 106px; top: 104px; width: 340px; height: 2px; background: var(--amber);
  }
  .person { position: absolute; left: 30px; top: 120px; }
  .person__name { font-weight: 700; font-size: 24px; color: var(--orange); line-height: 1; }
  .person__title { font-style: italic; font-size: 15px; color: var(--white); margin-top: 2px; }
  .divider {
    position: absolute; left: 200px; top: 140px; width: 390px; height: 1.5px; background: var(--amber);
  }
  .contact { position: absolute; left: 30px; top: 176px; list-style: none; }
  .contact__item {
    display: flex; align-items: center; gap: 12px;
    font-size: 16px; color: var(--white); line-height: 22px;
  }
  .contact__icon { width: 12px; height: 12px; fill: var(--orange); flex: none; }
  .address {
    position: absolute; right: 30px; bottom: 34px;
    text-align: right; font-size: 17px; color: var(--white); line-height: 21px;
  }
  .edge-band {
    position: absolute; left: 0; right: 0; bottom: 0; height: 10px;
    background: linear-gradient(90deg, var(--orange) 0%, var(--orange) 70%, var(--amber) 100%);
  }
</style>
</head>
<body>
  <section class="card card--front">
    <div class="front-mark">
      <div class="front-mark__square"></div>
      <div class="front-mark__name">Lanternfield<br>Drinks</div>
    </div>
  </section>

  <section class="card card--back">
    <div class="brand">
      <div class="brand__square"></div>
      <div class="brand__name">Lanternfield Drinks Co.</div>
    </div>
    <div class="brand__rule"></div>

    <div class="person">
      <div class="person__name">Avery Hollins</div>
      <div class="person__title">Managing Director</div>
    </div>
    <div class="divider"></div>

    <ul class="contact">
      <li class="contact__item">
        <svg class="contact__icon" viewBox="0 0 12 12"><path d="M1 4c0-2 1-3 3-3l1 2-1 1c.5 1.5 1.5 2.5 3 3l1-1 2 1c0 2-1 3-3 3C3 10 1 7 1 4z"/></svg>
        555.210.4837
      </li>
      <li class="contact__item">
        <svg class="contact__icon" viewBox="0 0 12 12"><rect x="3" y="0.5" width="6" height="11" rx="1"/><rect x="4" y="2" width="4" height="6" fill="#1d1d1f"/></svg>
        555.392.6614
      </li>
      <li class="contact__item">
        <svg class="contact__icon" viewBox="0 0 12 12"><rect x="0.5" y="2.5" width="11" height="7"/><path d="M0.5 2.5 6 7l5.5-4.5" fill="none" stroke="#1d1d1f" stroke-width="1"/></svg>
        avery@lanternfielddrinks.com
      </li>
      <li class="contact__item">
        <svg class="contact__icon" viewBox="0 0 12 12"><circle cx="6" cy="6" r="5.5"/><path d="M0.5 6h11M6 0.5c-2.5 3-2.5 8 0 11M6 0.5c2.5 3 2.5 8 0 11" fill="none" stroke="#1d1d1f" stroke-width=".8"/></svg>
        www.lanternfielddrinks.com
      </li>
    </ul>

    <address class="address" style="font-style:normal">
      418 Millbrook Ave.,<br>Fairhaven, US 204816
    </address>
    <div class="edge-band"></div>
  </section>
</body>
</html>
```